Theatrical Illusion Show poster

For a new proffesional magic show that will be made in a theater in Switzerland we need a design of a poster. This posters will be out all over the city. It will be printed in A3.
The show is all about shadows and is not a traditional magic show but a contemporary fusion of magic, mentalism, storytelling and shadowplay. No cliche glitter and glamour las vegas style, but meaningfull theaterical piece. It should be clean proffesional. Not have a feel its AI generated..
Text should be like in the example poster. The design can also be exactly like the example we Included here. We like the design to be simpel. For example a white background, a spotlight from the front, and two shadows that act diffrent than the magician. Butterflys are important in the story and should be included.
Foto of the artist on the poster is not obligatory.
Text :
Die flüsternde Laterne
Lorenz Albrecht
Fesselndes Zauber-Theater
27. bis 30. Mai 2026 - 20:00 - Turmsaal St. Gallen
Tickets: www.turmsaal-buehne.ch - 071 48 62 17

Target Market(s)

Familie audience - Cultural intrested people

Industry/Entity Type

Theater, art, entertainment

Requirements
Must have
• The shadows in the background should do something diffrent. Butterflys in shadow. Name of the show, artist name and 5 cm space down for date, time, place etc.
Should not have
• It should not be very colourfull or over the top cliche magician poster.

```html
<!DOCTYPE html>
<html lang="de">
<head>
<meta charset="utf-8">
<title>Die flüsternde Laterne – Lorenz Albrecht</title>
<link rel="stylesheet" href="https://fonts.googleapis.com/css2?family=Playfair+Display:wght@400;500&family=Barlow+Semi+Condensed:wght@400&display=swap">
<style>
  :root {
    --night: #16130f;
    --night-deep: #0c0b09;
    --cream: #f3e9d6;
    --spot-core: #fbf6ec;
    --spot-mid: #eadfc9;
    --ring: #e8d3ad;
    --shade: 44, 38, 31;
    --glow: 246, 232, 205;
  }
  html, body {
    margin: 0;
    padding: 0;
    overflow: hidden;
    background: var(--night-deep);
  }
  .poster {
    position: relative;
    width: 670px;
    height: 1200px;
    overflow: hidden;
    background: radial-gradient(ellipse at 50% 40%, #221e19 0%, var(--night) 55%, var(--night-deep) 100%);
    color: var(--cream);
    font-family: "Playfair Display", Georgia, serif;
  }
  .halo {
    position: absolute;
    left: 0;
    top: 0;
    width: 670px;
    height: 1200px;
  }
  .stage-art {
    position: absolute;
    left: 0;
    top: 0;
    width: 670px;
    height: 1200px;
  }
  .stage-art .spotlight {
    position: absolute;
    left: 37px;
    top: 385px;
    width: 596px;
    height: 596px;
    border-radius: 50%;
    background: radial-gradient(circle, var(--spot-core) 0%, var(--spot-mid) 70%, rgba(234,223,201,0.6) 86%, rgba(234,223,201,0) 100%);
    filter: blur(6px);
  }
  .stage-art .shadow-figure {
    position: absolute;
    left: 110px;
    top: 480px;
    width: 470px;
    height: 520px;
    border-radius: 46% 46% 40% 40%;
    background: radial-gradient(ellipse at 45% 45%, rgba(var(--shade),0.7) 0%, rgba(var(--shade),0.45) 45%, rgba(var(--shade),0) 75%);
    filter: blur(14px);
  }
  .stage-art .butterfly-trail {
    position: absolute;
    left: 440px;
    top: 40px;
    width: 150px;
    height: 460px;
    border-radius: 50%;
    transform: rotate(14deg);
    background: radial-gradient(ellipse, rgba(var(--glow),0.35) 0%, rgba(var(--glow),0.12) 50%, rgba(var(--glow),0) 75%);
    filter: blur(10px);
  }
  .stage-art .butterfly-shadows {
    position: absolute;
    left: 395px;
    top: 465px;
    width: 130px;
    height: 220px;
    border-radius: 50%;
    background: radial-gradient(ellipse, rgba(var(--shade),0.45) 0%, rgba(var(--shade),0) 70%);
    filter: blur(10px);
  }
  .stage-art .floor-fade {
    position: absolute;
    left: 0;
    bottom: 0;
    width: 670px;
    height: 330px;
    background: linear-gradient(to bottom, rgba(12,11,9,0) 0%, rgba(12,11,9,0.85) 55%, var(--night-deep) 100%);
  }
  .title-block {
    position: absolute;
    top: 68px;
    left: 0;
    width: 670px;
    text-align: center;
  }
  .show-title {
    margin: 0;
    font-weight: 400;
    font-size: 70px;
    line-height: 67px;
    letter-spacing: -0.5px;
  }
  .artist-name {
    margin: 18px 0 0;
    font-weight: 400;
    font-size: 35px;
    line-height: 40px;
  }
  .show-genre {
    margin: 2px 0 0;
    font-weight: 400;
    font-size: 24px;
    line-height: 32px;
  }
  .details {
    position: absolute;
    bottom: 40px;
    left: 0;
    width: 670px;
    text-align: center;
    font-family: "Barlow Semi Condensed", "Arial Narrow", sans-serif;
    font-size: 26px;
    line-height: 31px;
  }
  .details p { margin: 0; }
</style>
</head>
<body>
  <main class="poster">
    <svg class="halo" viewBox="0 0 670 1200" aria-hidden="true">
      <defs>
        <linearGradient id="ring-fade" x1="0" y1="0" x2="0" y2="1">
          <stop offset="0" stop-color="var(--ring)" stop-opacity="0.85"/>
          <stop offset="0.7" stop-color="var(--ring)" stop-opacity="0.45"/>
          <stop offset="1" stop-color="var(--ring)" stop-opacity="0"/>
        </linearGradient>
        <filter id="ring-glow" x="-20%" y="-20%" width="140%" height="140%">
          <feGaussianBlur stdDeviation="4"/>
        </filter>
      </defs>
      <circle cx="360" cy="250" r="258" fill="none" stroke="url(#ring-fade)" stroke-width="6" filter="url(#ring-glow)" opacity="0.6"/>
      <circle cx="360" cy="250" r="258" fill="none" stroke="url(#ring-fade)" stroke-width="1.2"/>
    </svg>

    <div class="stage-art" role="img" aria-label="Magician in waistcoat lifting a top hat in a spotlight; his shadow on the wall behind him releases a trail of shadow butterflies that turn to glowing butterflies as they rise along the halo">
      <div class="spotlight"></div>
      <div class="shadow-figure"></div>
      <div class="butterfly-shadows"></div>
      <div class="butterfly-trail"></div>
      <div class="floor-fade"></div>
    </div>

    <header class="title-block">
      <h1 class="show-title">Die<br>flüsternde<br>Laterne</h1>
      <p class="artist-name">Lorenz Albrecht</p>
      <p class="show-genre">Fesselndes Zauber-Theater</p>
    </header>

    <footer class="details">
      <p>27. bis 30. Mai 2026 – 20:00 – Turmsaal St. Gallen</p>
      <p>Tickets: www.turmsaal-buehne.ch – 071 48 62 17</p>
    </footer>
  </main>
</body>
</html>
```